Meadowlark Hollow Candle Company needs a Label design

We need a label design for a new candle company based in Charleston South Carolina. Our mission is to provide people with candles that will fill any space with fragrances that are uplifting, comforting, fresh and will make any space feel like home. Our candles are aromatherapy, 100% soy wax, and hand poured (we would love for this to be indicated somewhere on the label). We would like to see a label that is modern, very clean and uses pastel colors like green, blush pink, mauve and blush blue. The final design should communicate peace, gratitude, hope, and happiness.

```html
<!DOCTYPE html>
<html lang="en">
<head>
<meta charset="UTF-8">
<title>Meadowlark Hollow Candle Company – Labels</title>
<link rel="stylesheet" href="https://fonts.googleapis.com/css2?family=Special+Elite&display=swap">
<style>
  :root {
    --bg: #f9f9f1;
    --label: #f3f4ef;
    --label-edge: #e4e6df;
    --lavender: #aca8c9;
    --lavender-text: #a6a2c4;
    --sage: #a9c6c1;
    --sage-text: #a2c2bd;
  }
  * { margin: 0; padding: 0; box-sizing: border-box; }
  html, body {
    width: 1200px;
    height: 900px;
    overflow: hidden;
    background: var(--bg);
  }
  .canvas {
    width: 1200px;
    height: 900px;
    display: flex;
    justify-content: center;
    align-items: center;
    gap: 44px;
  }
  .label {
    width: 330px;
    height: 430px;
    background: var(--label);
    border: 1px solid var(--label-edge);
    border-radius: 6px;
    display: flex;
    flex-direction: column;
    justify-content: center;
    padding: 0 28px 0 40px;
    font-family: "Special Elite", "Courier New", monospace;
  }
  .label-head {
    display: flex;
    align-items: center;
    gap: 14px;
  }
  .brand-square {
    width: 60px;
    height: 62px;
    flex: none;
    background: var(--accent);
  }
  .scent-name {
    font-size: 31px;
    line-height: 1.25;
    letter-spacing: 1px;
    color: var(--accent-text);
  }
  .brand-name {
    margin-top: 10px;
    font-size: 10px;
    letter-spacing: 1px;
    text-transform: uppercase;
    color: var(--accent-text);
  }
  .claims {
    margin-top: 12px;
    color: var(--accent-text);
    text-transform: uppercase;
  }
  .claims .tagline { font-size: 14.5px; letter-spacing: 0.5px; }
  .claims .details { font-size: 12px; margin-top: 6px; letter-spacing: 0.3px; }
  .label--lavender { --accent: var(--lavender); --accent-text: var(--lavender-text); }
  .label--sage { --accent: var(--sage); --accent-text: var(--sage-text); }
</style>
</head>
<body>
  <main class="canvas">
    <section class="label label--lavender">
      <div class="label-head">
        <span class="brand-square"></span>
        <h2 class="scent-name">Lavender<br>Vanilla</h2>
      </div>
      <p class="brand-name">Meadowlark Hollow Candle Company</p>
      <div class="claims">
        <p class="tagline">All Natural Aromatherapy</p>
        <p class="details">Hand Poured | 100% Soy Wax</p>
      </div>
    </section>

    <section class="label label--sage">
      <div class="label-head">
        <span class="brand-square"></span>
        <h2 class="scent-name">Eucalyptus<br>Mint</h2>
      </div>
      <p class="brand-name">Meadowlark Hollow Candle Company</p>
      <div class="claims">
        <p class="tagline">All Natural Aromatherapy</p>
        <p class="details">Hand Poured | 100% Soy Wax</p>
      </div>
    </section>
  </main>
</body>
</html>
```